Business Card Design For A Cajun Seafood Restaurant

We are opening a cajun seafood restaurant in a week. We mainly serve cajun seafood which is orginally from Louisiana. We want design on both sides of a business card. I have menu on the website. You can go to www.reednkettle.example to check out our menu.

Restaurant name: Reed N' Kettle
Phone: +1 (555) 304-7712
Address: 48206 Ludlow Row, #7, Bexmoor Flats, Ca90000
Email: reednkettle@mailbox.example
Website: www.reednkettle.example

Maybe add social media icons (facebook, instagram) if looks nice on the business card.
facebook.com/reednkettle
instagram.com/reednkettle or @reednkettle

Attached is the logo and other business card samples that I like.

```html
<!DOCTYPE html>
<html lang="en">
<head>
<meta charset="utf-8">
<title>Reed N' Kettle — Business Card</title>
<link href="https://fonts.googleapis.com/css2?family=Alfa+Slab+One&family=Open+Sans:wght@400;600&display=swap" rel="stylesheet">
<style>
  :root {
    --bg: #e9e6e2;
    --card-white: #f7f7f5;
    --card-black: #1c1c1c;
    --orange: #f26a1b;
    --ink: #2b2b2b;
    --cream: #f4f0e8;
    --crab-light: #f7a24a;
    --crab-dark: #d6501a;
  }
  * { margin: 0; padding: 0; box-sizing: border-box; }
  html, body { width: 1200px; height: 844px; overflow: hidden; }
  body {
    background: var(--bg);
    font-family: "Open Sans", Arial, sans-serif;
    position: relative;
  }
  .card {
    position: absolute;
    width: 525px;
    height: 300px;
    border-radius: 4px;
    box-shadow: 0 6px 18px rgba(0,0,0,.18);
    overflow: hidden;
  }
  .card--front { left: 60px; top: 272px; background: var(--card-white); }
  .card--back  { left: 615px; top: 272px; background: var(--card-black); }

  .brand-name {
    font-family: "Alfa Slab One", Georgia, serif;
    font-weight: 400;
    letter-spacing: 1px;
    text-transform: uppercase;
  }
  .front__title {
    position: absolute; left: 34px; top: 34px;
    font-size: 24px; color: var(--orange);
  }
  .contact {
    position: absolute; left: 34px; top: 82px;
    list-style: none; font-size: 12.5px; color: var(--ink); line-height: 1.35;
  }
  .contact li { display: flex; align-items: center; gap: 7px; }
  .contact svg { width: 10px; height: 10px; flex: none; }
  .address {
    position: absolute; left: 34px; top: 150px;
    font-size: 13px; color: var(--ink); line-height: 1.4; font-style: normal;
  }
  .social {
    position: absolute; left: 34px; top: 222px; list-style: none;
    font-size: 17px; color: var(--ink); line-height: 1.75;
  }
  .social li { display: flex; align-items: center; gap: 8px; }
  .social__mark { width: 17px; height: 17px; border-radius: 3px; background: var(--orange); flex: none; }

  .logo {
    position: absolute; display: flex; flex-direction: column; align-items: center;
  }
  .logo__art {
    width: 120px; height: 110px; border-radius: 50%;
    background: radial-gradient(circle at 45% 40%, var(--crab-light), var(--crab-dark));
  }
  .logo__name { margin-top: 10px; font-size: 21px; }
  .card--front .logo { left: 300px; top: 70px; width: 200px; }
  .card--front .logo__name { color: var(--ink); }
  .card--back .logo { left: 0; top: 58px; width: 100%; }
  .card--back .logo__name { color: var(--cream); }
</style>
</head>
<body>
  <section class="card card--front" aria-label="Card front">
    <h1 class="brand-name front__title">Reed N' Kettle</h1>
    <ul class="contact">
      <li><svg viewBox="0 0 10 10"><path d="M2 0.5 L4 2.5 L3 4 Q4.5 6 6 7 L7.5 6 L9.5 8 L8 9.5 Q3 9 0.5 2 Z" fill="var(--orange)"/></svg>+1 (555) 304-7712</li>
      <li><svg viewBox="0 0 10 10"><rect x="0.5" y="2" width="9" height="6.5" rx="1" fill="var(--orange)"/><path d="M1 2.5 L5 5.5 L9 2.5" stroke="#fff" stroke-width="1" fill="none"/></svg>reednkettle@mailbox.example</li>
      <li><svg viewBox="0 0 10 10"><circle cx="5" cy="5" r="4.5" fill="var(--orange)"/><path d="M1 5 H9 M5 0.5 V9.5" stroke="#fff" stroke-width=".8"/></svg>www.reednkettle.example</li>
    </ul>
    <address class="address">48206 Ludlow Row,<br>#7, Bexmoor Flats, Ca90000</address>
    <ul class="social">
      <li><span class="social__mark"></span>/reednkettle</li>
      <li><span class="social__mark"></span>/reednkettle</li>
    </ul>
    <div class="logo">
      <div class="logo__art" role="img" aria-label="Illustrated cartoon crab holding corn cobs"></div>
      <span class="brand-name logo__name">Reed N' Kettle</span>
    </div>
  </section>

  <section class="card card--back" aria-label="Card back">
    <div class="logo">
      <div class="logo__art" role="img" aria-label="Illustrated cartoon crab holding corn cobs"></div>
      <span class="brand-name logo__name">Reed N' Kettle</span>
    </div>
  </section>
</body>
</html>
```